Label Craft Beer with CBD

Create a label for our cbd (cannabidiol) beer. We do have a first / simple idea. now it needs a professional finish. Please show your very own idea as well, because ours is only a draft and we need YOUR HELP! size front: H 8 cm, W 7 cm size back: H 7.5 cm, W 5.5 cm

```html
<!DOCTYPE html>
<html lang="en">
<head>
<meta charset="utf-8">
<title>Velda Brew – Premium Lager Labels</title>
<link href="https://fonts.googleapis.com/css2?family=Oswald:wght@300;400;600&display=swap" rel="stylesheet">
<style>
  :root {
    --page-bg: #e8e8e6;
    --label-bg: #4b4744;
    --label-edge: #57524e;
    --ink-light: #f1efec;
    --ink-muted: #cfcac5;
    --accent-red: #d9535a;
    --accent-green: #9cc495;
    --accent-orange: #ef9a55;
  }
  * { margin: 0; padding: 0; box-sizing: border-box; }
  html, body {
    width: 1200px;
    height: 1088px;
    overflow: hidden;
    background: var(--page-bg);
    font-family: "Oswald", "Arial Narrow", sans-serif;
  }
  .label-row {
    position: absolute;
    inset: 0;
    display: flex;
    justify-content: center;
    align-items: center;
    gap: 40px;
  }
  .label {
    position: relative;
    width: 340px;
    height: 560px;
    background: linear-gradient(90deg, var(--label-bg), var(--label-edge) 50%, var(--label-bg));
    display: flex;
    flex-direction: column;
    align-items: center;
    color: var(--ink-light);
  }
  .label--red { --accent: var(--accent-red); }
  .label--green { --accent: var(--accent-green); }
  .label--orange { --accent: var(--accent-orange); }

  .origin-mark {
    margin-top: 36px;
    height: 22px;
    display: flex;
    align-items: center;
    gap: 8px;
    font-size: 12px;
    font-weight: 400;
    letter-spacing: 0.5px;
    color: var(--ink-muted);
  }
  .origin-mark .rule { width: 10px; height: 1px; background: var(--ink-muted); }
  .origin-mark svg { display: block; }

  .brand {
    margin-top: 30px;
    display: flex;
    flex-direction: column;
    align-items: center;
    gap: 20px;
  }
  .brand-circle {
    width: 190px;
    height: 190px;
    border-radius: 50%;
    border: 5px solid var(--accent);
  }
  .brand-name {
    font-size: 40px;
    font-weight: 600;
    letter-spacing: 2px;
    color: var(--accent);
    line-height: 1;
    white-space: nowrap;
  }

  /* side notes sit beside the circle only: circle spans y 88–278 */
  .side-note {
    position: absolute;
    top: 93px;
    height: 180px;
    writing-mode: vertical-rl;
    text-align: center;
    font-size: 10px;
    font-weight: 400;
    letter-spacing: 0.5px;
    line-height: 12px;
    white-space: nowrap;
    color: var(--ink-muted);
  }
  .side-note--left { left: 26px; transform: rotate(180deg); }
  .side-note--right { right: 26px; }

  .style-name {
    margin-top: 34px;
    font-size: 30px;
    font-weight: 600;
    line-height: 1;
    letter-spacing: 0.5px;
  }
  .style-note {
    margin-top: 10px;
    font-size: 23px;
    font-weight: 300;
    color: var(--ink-muted);
    line-height: 1;
  }
</style>
</head>
<body>
<main class="label-row">
  <article class="label label--red">
    <div class="origin-mark"><span>SWISS</span><span class="rule"></span>
      <svg width="22" height="22" viewBox="0 0 22 22" aria-hidden="true"><rect width="22" height="22" rx="4" fill="#f1efec"/><rect x="9" y="4" width="4" height="14" fill="#4b4744"/><rect x="4" y="9" width="14" height="4" fill="#4b4744"/></svg>
      <span class="rule"></span><span>MADE</span></div>
    <div class="brand"><div class="brand-circle"></div><div class="brand-name">VELDA BREW</div></div>
    <p class="side-note side-note--left">WELL BEING · NO THC · NO HANG OVER</p>
    <p class="side-note side-note--right">10 MG CBD · 4.3% ALC · 330 CL</p>
    <h2 class="style-name">PREMIUM LAGER</h2>
    <p class="style-note">NATURTRÜB</p>
  </article>

  <article class="label label--green">
    <div class="origin-mark"><span>SWISS</span><span class="rule"></span>
      <svg width="22" height="22" viewBox="0 0 22 22" aria-hidden="true"><rect width="22" height="22" rx="4" fill="#f1efec"/><rect x="9" y="4" width="4" height="14" fill="#4b4744"/><rect x="4" y="9" width="14" height="4" fill="#4b4744"/></svg>
      <span class="rule"></span><span>MADE</span></div>
    <div class="brand"><div class="brand-circle"></div><div class="brand-name">VELDA BREW</div></div>
    <p class="side-note side-note--left">WELL BEING · NO THC · NO HANG OVER</p>
    <p class="side-note side-note--right">10 MG CBD · 4.3% ALC · 330 CL</p>
    <h2 class="style-name">PREMIUM LAGER</h2>
    <p class="style-note">NATURTRÜB</p>
  </article>

  <article class="label label--orange">
    <div class="origin-mark"><span>SWISS</span><span class="rule"></span>
      <svg width="22" height="22" viewBox="0 0 22 22" aria-hidden="true"><rect width="22" height="22" rx="4" fill="#f1efec"/><rect x="9" y="4" width="4" height="14" fill="#4b4744"/><rect x="4" y="9" width="14" height="4" fill="#4b4744"/></svg>
      <span class="rule"></span><span>MADE</span></div>
    <div class="brand"><div class="brand-circle"></div><div class="brand-name">VELDA BREW</div></div>
    <p class="side-note side-note--left">WELL BEING · NO THC · NO HANG OVER</p>
    <p class="side-note side-note--right">10 MG CBD · 4.3% ALC · 330 CL</p>
    <h2 class="style-name">PREMIUM LAGER</h2>
    <p class="style-note">NATURTRÜB</p>
  </article>
</main>
</body>
</html>
```